Flyer-Design für Schädlingsbekämpfung
Sehr gute Kommunikation! Produkt sehr gut!! Gerne wieder
Zielgruppe
Schädlingsbekämpfung- und Prophylaxe, Service Monitoring, Gastronomie und Industrie, alle Lebendsmittel verarbeitenden Betriebe
Aufgabenstellung
Schwerpunkt soll das HACCP Konzept sein, welches bei allen Lebensmittelverarbeiteten Betrieben gesetzlich vorgeschrieben ist,

```html
<!DOCTYPE html>
<html lang="de">
<head>
<meta charset="utf-8">
<title>Schädlingsfrei Jonas Walberg – HACCP Flyer</title>
<link href="https://fonts.googleapis.com/css2?family=Arimo:wght@400;700&family=Cabin:wght@500;700&family=Pathway+Gothic+One&display=swap" rel="stylesheet">
<style>
  :root{
    --paper:#ffffff;
    --mist:#e4e4e7;
    --steel:#8591b5;
    --slate:#2f3241;
    --ink:#26262c;
    --sand:#cdb88f;
    --leaf:#2f8a3e;
    --alarm:#c8161d;
    --outline:#2a2d3c;
  }
  *{margin:0;padding:0;box-sizing:border-box}
  html,body{width:1200px;height:849px;overflow:hidden;background:var(--paper)}
  .flyer{position:relative;width:1200px;height:849px;overflow:hidden;background:var(--paper)}
  .art{position:absolute;left:0;top:0}

  .brand{position:absolute;left:290px;top:182px;width:291px;height:88px;background:var(--paper);display:flex;align-items:center;gap:12px;padding:0 12px;font-family:"Cabin",sans-serif;font-weight:700;color:var(--ink)}
  .brand-mark{width:62px;height:62px;border-radius:50%;background:var(--leaf);flex:none}
  .brand-name{font-size:18px;line-height:21px}
  .brand-name span{display:block;white-space:nowrap}

  .promises{position:absolute;left:50px;top:420px;width:230px;font-family:"Pathway Gothic One",sans-serif;color:var(--sand);font-size:17px;text-align:center}
  .promises li{list-style:none;position:absolute;left:0;width:230px;white-space:nowrap}

  .feature-icons{position:absolute;top:623px;height:34px;background:var(--leaf);display:flex;align-items:center;justify-content:center}
  .feature-icons svg{width:22px;height:22px}

  .haccp-info{position:absolute;left:325px;top:417px;width:245px;font-family:"Cabin",sans-serif;color:var(--ink)}
  .haccp-info h2{font-size:12.5px;font-weight:700;text-align:center;line-height:15px;width:245px}
  .haccp-info p{margin-top:11px;font-size:12.5px;font-weight:500;line-height:16.5px}

  .contact-item{position:absolute;top:812px;font-family:"Pathway Gothic One",sans-serif;font-size:14px;color:var(--ink);text-align:center;white-space:nowrap}

  .hotline{position:absolute;left:700px;top:59px;width:161px;height:31px;border:1.5px solid var(--ink);background:var(--paper);font-family:"Arimo",sans-serif;font-weight:700;color:var(--alarm);font-size:16px;display:flex;align-items:center;justify-content:center}

  .services{position:absolute;left:758px;top:567px;width:442px;height:282px;background:var(--paper);padding:8px 0 0 20px;font-family:"Arimo",sans-serif;color:var(--ink);font-size:28px;line-height:35.5px}
  .services li{list-style:none;white-space:nowrap}
  .services li::before{content:"\2713";font-size:17px;margin-right:10px;position:relative;top:-3px}
  .services .focus{font-weight:700;color:var(--alarm)}
</style>
</head>
<body>
<div class="flyer">

  <svg class="art" width="1200" height="849" viewBox="0 0 1200 849">
    <defs>
      <linearGradient id="greyFade" x1="0" y1="0" x2="1" y2="1">
        <stop offset="0" stop-color="#f3f3f4"/>
        <stop offset="1" stop-color="#c9c9cd"/>
      </linearGradient>
      <linearGradient id="shadowFade" x1="0" y1="0" x2="1" y2="0">
        <stop offset="0" stop-color="#ffffff" stop-opacity="0"/>
        <stop offset="1" stop-color="#55576a"/>
      </linearGradient>
    </defs>

    <rect x="16" y="4" width="577" height="722" fill="var(--mist)"/>
    <polygon points="330,4 593,4 593,400 460,400" fill="url(#greyFade)"/>
    <polygon points="370,4 520,150 593,80 593,4" fill="#d2d2d6"/>
    <polygon points="420,290 593,290 593,400 500,400" fill="url(#shadowFade)" opacity=".55"/>
    <polygon points="16,4 330,4 249,332 16,332" fill="var(--paper)"/>
    <rect x="16" y="401" width="577" height="195" fill="var(--steel)"/>
    <polygon points="120,728 593,728 580,742 120,742" fill="url(#shadowFade)" opacity=".5"/>

    <rect x="438" y="32" width="90" height="90" rx="16" transform="rotate(45 479 78)" fill="none" stroke="var(--outline)" stroke-width="2.5"/>
    <rect x="520" y="52" width="60" height="60" rx="14" transform="rotate(45 550 82)" fill="var(--steel)" opacity=".95"/>
    <rect x="415" y="300" width="75" height="75" rx="14" transform="rotate(45 455 339)" fill="none" stroke="var(--outline)" stroke-width="2.5"/>

    <polygon points="63,36 321,36 261,287 0,287" fill="#8e8e90" role="img" aria-label="Foto: Schädlingsbekämpfer im Schutzanzug sprüht an einer Hauswand"/>

    <rect x="50" y="354" width="230" height="372" fill="var(--slate)"/>

    <polygon points="344,627 536,627 580,719 536,811 344,811 298,719" fill="#c9b9a6" role="img" aria-label="Foto: Schädlingsbekämpfer mit Atemschutz behandelt einen Raum"/>

    <polygon points="3,776 330,776 360,811 414,849 3,849" fill="var(--steel)"/>
    <line x1="111" y1="784" x2="111" y2="842" stroke="var(--paper)" stroke-width="1.5"/>
    <line x1="213" y1="784" x2="213" y2="842" stroke="var(--paper)" stroke-width="1.5"/>
    <circle cx="55" cy="797" r="13" fill="var(--paper)"/>
    <path d="M48 801 L48 795 L55 790 L62 795 L62 801 Z M48 795 L55 799 L62 795" fill="var(--slate)" stroke="var(--paper)" stroke-width="1"/>
    <circle cx="159" cy="799" r="13" fill="var(--paper)" stroke="var(--ink)" stroke-width="1.5"/>
    <path d="M153 792 c-2 3 1 10 7 13 l3-3 -3-3 -2 1 c-2-1-3-3-4-5 l1-2 -3-3 z" fill="var(--ink)"/>

    <rect x="620" y="0" width="580" height="849" fill="#f2f2f4"/>
    <polygon points="620,0 690,0 620,75" fill="var(--steel)"/>
    <polygon points="620,460 758,410 758,849 620,849" fill="var(--steel)"/>
    <polygon points="700,380 850,330 900,567 758,567" fill="#e0e0e4"/>
    <polygon points="1000,420 1200,300 1200,567 900,567" fill="url(#greyFade)"/>

    <rect x="700" y="228" width="60" height="60" rx="14" transform="rotate(45 730 258)" fill="var(--steel)"/>
    <rect x="662" y="273" width="92" height="92" rx="16" transform="rotate(45 708 319)" fill="none" stroke="var(--outline)" stroke-width="2.5"/>
    <rect x="1070" y="465" width="50" height="50" rx="12" transform="rotate(45 1095 490)" fill="var(--steel)" opacity=".6"/>
    <rect x="1100" y="443" width="94" height="94" rx="16" transform="rotate(45 1147 490)" fill="none" stroke="var(--outline)" stroke-width="2.5"/>

    <path d="M1010 0 L1200 0 L1200 240 L1045 440 Q1019 472 993 446 L806 259 Q780 235 806 210 Z" fill="#8c6b48" role="img" aria-label="Foto: Wespen auf einer Wabe"/>

    <circle cx="771" cy="468" r="101" fill="#7f9a6a" role="img" aria-label="Foto: Sprühdüse besprüht einen Zweig mit Blättern"/>

    <rect x="670" y="57" width="17" height="33" rx="4" fill="none" stroke="var(--ink)" stroke-width="2"/>
    <path d="M675 67 c-1 2 1 7 5 9 l2-2 -2-2 -1 1 c-1-1-2-2-3-4 l1-1 -2-2 z" fill="var(--ink)"/>
  </svg>

  <div class="brand">
    <span class="brand-mark"></span>
    <div class="brand-name"><span>Schädlingsfrei</span><span>Jonas Walberg</span><span>Bad Lindenau</span></div>
  </div>

  <ul class="promises">
    <li style="top:15px">HACCP-Monitoring &amp; Dokumentation</li>
    <li style="top:67px">Schnell, nachhaltig und einfach</li>
    <li style="top:128px">Fachgerechte Bekämpfung mit Erfahrung</li>
  </ul>

  <div class="feature-icons" style="left:70px;width:58px">
    <svg viewBox="0 0 24 24"><circle cx="12" cy="12" r="9" fill="none" stroke="#111" stroke-width="2.5"/><path d="M7 9 l5 5 6-8" fill="none" stroke="#111" stroke-width="2.5"/></svg>
  </div>
  <div class="feature-icons" style="left:133px;width:67px">
    <svg viewBox="0 0 24 24"><rect x="8" y="8" width="8" height="14" rx="1" fill="#111"/><rect x="10" y="4" width="4" height="4" fill="#111"/></svg>
  </div>
  <div class="feature-icons" style="left:205px;width:58px">
    <svg viewBox="0 0 24 24"><circle cx="11" cy="13" r="8" fill="none" stroke="#111" stroke-width="2.5"/><path d="M11 9v4h4M9 3h4M16 11h6M16 15h6" stroke="#111" stroke-width="2"/></svg>
  </div>

  <section class="haccp-info">
    <h2>HACCP-Konzept für Ihren Betrieb:<br>gesetzlich vorgeschrieben, sicher erfüllt</h2>
    <p>Für alle Lebensmittel verarbeitenden Betriebe ist das HACCP-Konzept Pflicht. Wir übernehmen Monitoring, Prophylaxe und lückenlose Dokumentation für Gastronomie und Industrie – regelmäßig, prüfsicher und zuverlässig. Auch bei Wespen und anderen Schädlingen helfen wir schnell.</p>
  </section>

  <div class="contact-item" style="left:6px;width:100px">walberg@jw-sf.de</div>
  <div class="contact-item" style="left:114px;width:96px">0671 / 884 61 302</div>

  <div class="hotline">0152 / 418 73 290</div>

  <ul class="services">
    <li class="focus">HACCP Service</li>
    <li>Schädlingsbekämpfung</li>
    <li>Holz- und Bautenschutz</li>
    <li>Hausbockbekämpfung</li>
    <li>Hausschwammbekämpfung</li>
    <li>Pilz/ Schimmelpilzsanierung</li>
    <li>Taubenabwehr</li>
  </ul>
</div>
</body>
</html>
```